Business Card Design

I already have a company logo for my company. I have a logo for the manufacturer we represent. I want a professional business card design.

```html
<!DOCTYPE html>
<html lang="en">
<head>
<meta charset="utf-8">
<title>Signalguard Solutions – Business Card</title>
<link href="https://fonts.googleapis.com/css2?family=Open+Sans:wght@400;600;700&display=swap" rel="stylesheet">
<style>
  :root{
    --stage:#232323;
    --card-white:#ffffff;
    --brand-red:#e31e26;
    --brand-red-deep:#c9161d;
    --brand-orange:#f07a3a;
    --brand-gold:#b8902f;
    --ink:#1b1b1b;
  }
  *{box-sizing:border-box;margin:0;padding:0}
  html,body{width:1200px;height:780px;overflow:hidden;background:var(--stage)}
  body{font-family:"Open Sans",Arial,sans-serif;display:flex;align-items:center;justify-content:center;gap:40px}
  .card{width:540px;height:310px;border-radius:22px;position:relative;overflow:hidden}

  /* Front */
  .card-front{background:var(--card-white)}
  .company-mark{position:absolute;left:150px;top:52px;display:flex;align-items:center;gap:12px}
  .company-mark__dot{width:34px;height:34px;border-radius:50%;background:var(--brand-red)}
  .company-mark__name{font-weight:700;font-size:22px;line-height:1.1;color:var(--brand-red);width:170px}
  .info-band{position:absolute;left:0;top:160px;width:540px;height:88px}
  .info-band svg{position:absolute;inset:0}
  .person{position:absolute;left:26px;top:174px;white-space:nowrap}
  .person__name{font-weight:700;font-size:22px;color:var(--brand-red);line-height:1.2}
  .person__title{font-weight:400;font-size:14px;color:var(--card-white);line-height:1.4}
  .contacts{position:absolute;left:322px;top:170px;list-style:none;color:var(--card-white);font-size:15px;line-height:24px;white-space:nowrap}
  .contacts li{display:flex;align-items:center;gap:8px}
  .contacts svg{width:14px;height:14px;flex:none}
  .address{position:absolute;left:26px;top:262px;font-size:14.5px;color:var(--ink);white-space:nowrap}

  /* Back */
  .card-back{background:linear-gradient(100deg,var(--brand-red) 0%,var(--brand-red) 45%,var(--brand-red-deep) 70%,var(--brand-orange) 130%)}
  .back-pattern{position:absolute;inset:0;background:linear-gradient(160deg,rgba(240,122,58,0) 30%,rgba(240,122,58,.35) 100%)}
  .back-mark{position:absolute;right:30px;bottom:34px;font-weight:700;font-size:11px;color:var(--card-white);letter-spacing:.3px}
</style>
</head>
<body>

<section class="card card-front" aria-label="Business card front">
  <div class="company-mark">
    <span class="company-mark__dot"></span>
    <span class="company-mark__name">Signalguard Solutions LLC</span>
  </div>

  <div class="info-band">
    <svg viewBox="0 0 540 88" preserveAspectRatio="none">
      <polygon points="0,0 290,0 258,88 0,88" fill="var(--brand-gold)"/>
      <polygon points="302,0 540,0 540,88 270,88" fill="var(--brand-red)"/>
    </svg>
  </div>

  <div class="person">
    <p class="person__name">Marta Kovalenko</p>
    <p class="person__title">Managing Director</p>
  </div>

  <ul class="contacts">
    <li>
      <svg viewBox="0 0 24 24"><path fill="#fff" d="M6.6 10.8a15.1 15.1 0 0 0 6.6 6.6l2.2-2.2a1 1 0 0 1 1-.25 11.4 11.4 0 0 0 3.6.57 1 1 0 0 1 1 1V20a1 1 0 0 1-1 1A17 17 0 0 1 3 4a1 1 0 0 1 1-1h3.5a1 1 0 0 1 1 1c0 1.250.2 2.45.57 3.57a1 1 0 0 1-.25 1z"/></svg>
      (555) 214-3870
    </li>
    <li>
      <svg viewBox="0 0 24 24"><path fill="#fff" d="M3 5h18v14H3z"/><path fill="none" stroke="var(--brand-red)" stroke-width="2" d="M3 6l9 7 9-7"/></svg>
      info@signalguardco.com
    </li>
    <li>
      <svg viewBox="0 0 24 24"><circle cx="12" cy="12" r="9" fill="none" stroke="#fff" stroke-width="2"/><path fill="none" stroke="#fff" stroke-width="1.6" d="M3 12h18M12 3c3 3 3 15 0 18M12 3c-3 3-3 15 0 18"/></svg>
      www.signalguardco.com
    </li>
  </ul>

  <p class="address">418 Harbor View Rd #12, Lakeport, FL 32001, USA</p>
</section>

<section class="card card-back" aria-label="Business card back">
  <div class="back-pattern" role="img" aria-label="Repeating brand pattern fading from red to orange"></div>
  <p class="back-mark">Signalguard Solutions</p>
</section>

</body>
</html>
```